Orthobiologic, StemCell, Bone Marrow Aspirate Device Distributor

We need a wordpress fully functioning website design for an innovative ortho-biologic, Bone Marrow Aspirate Device that extracts stem cells for orthopedic regenerative medical professionals. We also offer state of the art training in there office setting with licensed medical staff, a full service support team, and software for tracking patient outcome over time. We are an innovative company that prides itself on gold standard support. We will have other offerings on our website and would like a spot for "future" products. We would like to see designs that look professional, medical, and convey support, security, science, and innovation. We prefer shades of blue and red/orange. I particularly like the following websites that also sell the same device in order of preference:regenacelltherapy.comhttps://aspire-medical.eu/marrow-cellution/https://www.matrixbiosurgical.com/#emerging-solutions-in-healthcareElite2elite.comI have attached a few pictures of the device for reference

Target Market(s)

Orthopedics, Regenerative medicine doctors, Industry representatives, Hospitals

Industry/Entity Type

Medical Equipment

Coding

Coded - Design and coding required

Colors
3176b5
33a6d7
f37022
ec1f27

Requirements
Must have
• It must be able to have videos which I can supply, email, online ordering, and sfax. I have a domain name Coralweavesolutions.com . It must have a FAQ section which you can obtain some information from https://www.tolvenclinical.com/solutions#resources
• The device is manufactured by Dulmor and this is the link to the product page http://www.dulmor.com/quintadraw
• I am currently working on a custom logo and should be able to supply that in short order. I prefer shades of blue and red.
Nice to have
• I would love to have a graphic video as seen here: please see quinta draw vs bone marrow aspirate concentrate.
• https://www.tolvenclinical.com/solutions#competition
• I would pay considerably more to have something similar if it is at all possible
Should not have
• Nothing specific

```html
<!DOCTYPE html>
<html lang="en">
<head>
<meta charset="utf-8">
<title>Coralweave Solutions</title>
<link href="https://fonts.googleapis.com/css2?family=Montserrat:ital,wght@0,400;0,500;0,600;0,700;1,400&display=swap" rel="stylesheet">
<style>
:root{
  --blue:#1d4f8c;
  --blue-deep:#0f3367;
  --blue-bright:#3176b5;
  --cyan:#33a6d7;
  --red:#ec1f27;
  --orange:#f37022;
  --ink:#222;
  --text:#555;
  --light:#f4f4f4;
  --white:#fff;
}
*{box-sizing:border-box;margin:0;padding:0}
html,body{width:1200px;height:4971px;overflow:hidden}
body{position:relative;font-family:"Montserrat",sans-serif;color:var(--ink);background:var(--white)}
.abs{position:absolute}
.section-title{position:absolute;left:0;width:1200px;text-align:center;font-size:36px;font-weight:400}
.title-bar{position:absolute;left:573px;width:54px;height:3px;background:var(--ink)}

/* header */
.brand{left:145px;top:30px;display:flex;align-items:center;gap:14px}
.brand-dot{width:46px;height:46px;border-radius:50%;background:var(--blue-bright)}
.brand-name{font-size:24px;font-weight:600;color:var(--blue-bright);line-height:1.05}
.toll{left:598px;top:20px;display:flex;align-items:center;gap:12px}
.toll-icon{width:36px;height:36px;border-radius:50%;background:var(--red);display:flex;align-items:center;justify-content:center}
.toll small{display:block;font-size:11px;color:var(--text)}
.toll strong{font-size:22px;font-weight:600}
.quote-btn{left:845px;top:21px;width:211px;height:37px;border-radius:19px;background:var(--red);color:#fff;font-size:13px;font-weight:600;display:flex;align-items:center;justify-content:center;gap:6px}
.nav{top:84px;left:463px;display:flex;gap:0;font-size:18px}
.nav a{color:var(--ink);text-decoration:none;position:absolute;white-space:nowrap}

/* hero */
.hero{left:0;top:130px;width:1200px;height:600px;background:linear-gradient(90deg,#2a4a55 0%,#1f5a6a 30%,#6b5a4a 55%,#a14a22 80%,#2a3d70 100%)}
.hero-title{left:0;top:210px;width:1200px;text-align:center;color:#fff;font-size:58px;font-weight:500;line-height:66px}
.hero-btn{left:500px;top:368px;width:200px;height:36px;background:var(--red);color:#fff;font-size:14px;font-weight:500;display:flex;align-items:center;justify-content:center;border-radius:3px}
.dots{left:563px;top:440px;display:flex;gap:8px}
.dots span{width:18px;height:18px;border-radius:50%;border:2px solid #fff}
.dots span.on{background:#fff}

/* services */
.service-img{width:436px;height:270px;top:942px}
.service-card{top:1150px;width:407px;height:197px;background:#fff;box-shadow:0 4px 14px rgba(0,0,0,.12);text-align:center;clip-path:polygon(0 20px,50% 0,100% 20px,100% 100%,0 100%)}
.service-card h3{font-size:19px;font-weight:500;margin-top:34px}
.service-card p{font-size:13px;line-height:26px;color:var(--text);padding:10px 22px 0}

/* welcome */
.welcome{left:0;top:1452px;width:1200px;height:517px;background:linear-gradient(120deg,#0d2f63,#1d4f8c 60%,#133f7a)}
.welcome h2{left:145px;top:1556px;color:#fff;font-weight:400;font-size:33px;line-height:43px}
.welcome-text{left:145px;top:1655px;width:400px;color:#fff;font-size:14.5px;line-height:27px}
.read-more{left:145px;top:1816px;width:137px;height:39px;border:2px solid #fff;border-radius:20px;color:#fff;font-size:14px;display:flex;align-items:center;justify-content:center}
.video{left:596px;top:1553px;width:462px;height:300px;background:#fff;padding:8px}
.video-screen{width:446px;height:258px;background:linear-gradient(160deg,#d9606e,#c24a5a 60%,#9c3a48)}
.play{left:202px;top:108px;width:50px;height:50px;border-radius:50%;border:3px solid #fff;background:rgba(0,0,0,.45)}
.video-bar{height:26px;display:flex;align-items:center;gap:10px;padding:0 8px;font-size:8px;color:#777}

/* products */
.prod-ring{left:378px;top:2183px;width:432px;height:432px;border-radius:50%;background:#ececec}
.prod-core{left:430px;top:2235px;width:328px;height:328px;border-radius:50%;background:radial-gradient(circle at 50% 50%,#c0508c 0%,#7a4d8a 18%,#2b6cae 40%,#1c4f8a 75%,#163c6c 100%)}
.prod-node{width:124px;height:124px;border-radius:50%;background:#fff;border:6px solid #ececec}
.prod-node i{position:absolute;left:30px;top:22px;width:52px;height:70px;border-radius:6px;background:linear-gradient(#dfe4ea,#b9c2cc)}
.prod-label h4{font-size:19px;font-weight:500;margin-bottom:14px}
.prod-label p{font-size:13px;line-height:24px;color:var(--text)}
.prod-label.left{text-align:right;width:260px}
.prod-label.right{text-align:left;width:260px}

/* testimonials */
.clients{left:0;top:2718px;width:1200px;height:525px;background:linear-gradient(160deg,#0b1420,#122336 50%,#0b1726)}
.quote{width:300px;color:#fff}
.quote .bracket{position:absolute;left:0;top:-20px;width:24px;height:46px;border-left:2px solid #fff;border-top:2px solid #fff}
.quote p{padding-left:16px;font-style:italic;font-size:13.5px;line-height:24.5px}
.quote b{display:block;padding-left:16px;margin-top:12px;font-size:13px;font-style:italic;font-weight:600}
.quote .stars{padding-left:16px;margin-top:8px;font-size:14px;letter-spacing:3px}

/* faq */
.faq-bg{left:0;top:3243px;width:1200px;height:657px;background:linear-gradient(180deg,#eef2f6,#f7f9fb)}
.faq-item{left:193px;width:813px;background:#fff;border:1px solid #d9dde2;display:flex;align-items:center;padding-left:28px;gap:18px;font-size:14px;line-height:26px}
.faq-plus{flex:none;width:22px;height:22px;border-radius:50%;background:var(--blue-bright);position:relative}
.faq-plus::before,.faq-plus::after{content:"";position:absolute;background:#fff;left:5px;top:10px;width:12px;height:2px}
.faq-plus::after{left:10px;top:5px;width:2px;height:12px}

/* contact */
.contact{left:0;top:3900px;width:1200px;height:640px;background:linear-gradient(160deg,#1d4f8c,#2b62a5 50%,#1a4a88)}
.field{left:208px;width:383px;height:33px;background:#fff;font-size:9px;color:#777;padding:10px 14px}
.message{left:610px;top:4088px;width:382px;height:224px;background:#fff;font-size:9px;color:#777;padding:12px 14px}
.submit{left:488px;top:4356px;width:224px;height:39px;background:var(--red);color:#fff;font-size:14px;font-weight:600;display:flex;align-items:center;justify-content:center}

/* footer */
.foot-brand{left:100px;top:4586px;display:flex;align-items:center;gap:12px}
.foot-brand .brand-name{font-size:22px}
.socials{left:108px;top:4672px;display:flex;gap:6px}
.socials span{width:28px;height:28px;border-radius:50%;border:1px solid #888}
.foot-h{font-size:17px;font-weight:500}
.foot-p{font-size:11.5px;line-height:22px;color:var(--text)}
.news-input{left:338px;top:4680px;width:272px;height:40px;border:1px solid #ccc;border-radius:20px;font-size:9px;color:#777;padding:14px 16px}
.subscribe{left:338px;top:4732px;width:133px;height:35px;border-radius:18px;background:var(--blue-bright);color:#fff;font-size:13px;font-weight:600;display:flex;align-items:center;justify-content:center}
.c-row{left:656px;display:flex;gap:14px;font-size:12.5px;line-height:22px;color:#333}
.c-row svg{flex:none;margin-top:3px}
.links{left:959px;top:4618px;font-size:12.5px;line-height:27px;color:#333;list-style:none}
.copyright{left:0;top:4911px;width:1200px;text-align:center;font-size:12.5px;color:#333}
</style>
</head>
<body>

<!-- header -->
<div class="abs brand"><span class="brand-dot"></span><span class="brand-name">Coralweave<br>Solutions</span></div>
<div class="abs toll">
  <span class="toll-icon"><svg width="18" height="18" viewBox="0 0 24 24"><path fill="#fff" d="M6.6 10.8a15.2 15.2 0 0 0 6.6 6.6l2.2-2.2a1 1 0 0 1 1-.25 11.4 11.4 0 0 0 3.6.57 1 1 0 0 1 1 1V20a1 1 0 0 1-1 1A17 17 0 0 1 3 4a1 1 0 0 1 1-1h3.5a1 1 0 0 1 1 1c0 1.25.2 2.45.57 3.57a1 1 0 0 1-.25 1z"/></svg></span>
  <div><small>Toll free :</small><strong>808 0177 4290</strong></div>
</div>
<div class="abs quote-btn"><svg width="12" height="12" viewBox="0 0 24 24"><path fill="#fff" d="M3 17.2V21h3.8L17.8 9.9l-3.8-3.7zM20.7 7a1 1 0 0 0 0-1.4l-2.3-2.3a1 1 0 0 0-1.4 0l-1.8 1.8 3.7 3.8z"/></svg>REQUEST A QUOTE</div>
<nav class="abs nav">
  <a style="left:0">Home</a><a style="left:93px">About Us</a><a style="left:220px">Products</a><a style="left:338px">Blog</a><a style="left:417px">FAQ</a><a style="left:494px">Contact Us</a>
</nav>

<!-- hero -->
<div class="abs hero" role="img" aria-label="Wireframe human figure over a digital science background"></div>
<h1 class="abs hero-title">AUTOLOGOUS<br>STEM CELLTHERAPY</h1>
<div class="abs hero-btn">REQUEST A QUOTE</div>
<div class="abs dots" style="top:570px"><span class="on"></span><span></span><span></span></div>

<!-- services -->
<h2 class="section-title" style="top:806px">Our Services</h2>
<div class="title-bar" style="top:880px"></div>
<div class="abs service-img" style="left:145px;background:linear-gradient(135deg,#1d3a6b,#2a4f86 45%,#b45a8a 80%,#d98aa8)" role="img" aria-label="Microscopic view of cells and a DNA strand"></div>
<div class="abs service-img" style="left:620px;background:linear-gradient(135deg,#0d2a55,#1f4f88 45%,#b25a2a 80%,#e08a3a)" role="img" aria-label="Glowing human body outline on a dark background"></div>
<div class="abs service-card" style="left:160px"><h3>Cell Based Therapies</h3><p>Sed ut perspiciatis unde omnis iste natus error sit voluptatem accusantium doloremque laudantium, totam rem aperiam, eaque ipsa quae ab illo inventore veritatis et quasi architecto beatae vitae dicta dolores</p></div>
<div class="abs service-card" style="left:635px"><h3>Factor Based Therapies</h3><p>Sed ut perspiciatis unde omnis iste natus error sit voluptatem accusantium doloremque laudantium, totam rem aperiam, eaque ipsa quae ab illo inventore veritatis et quasi architecto beatae vitae dicta dolores</p></div>

<!-- welcome -->
<div class="abs welcome" role="img" aria-label="Deep blue background with faint cell imagery"></div>
<div class="welcome"><h2 class="abs" style="left:145px;top:1556px">Welcome to<br>Coralweave Solutions</h2></div>
<p class="abs welcome-text">Sed ut perspiciatis unde omnis iste natus error sit voluptatem accusantium doloremque laudantium, totam rem aperiam, eaque ipsa quae ab illo inventore veritatis et quasi architecto beatae vitae dicta sunt explicabo. Nemo enim ipsam voluptatem quia voluptas</p>
<div class="abs read-more">Read More</div>
<div class="abs video">
  <div class="video-screen" role="img" aria-label="Animated video still of a needle drawing marrow from bone" style="position:relative">
    <div class="abs play"><svg width="44" height="44" viewBox="0 0 44 44" style="position:absolute;left:0;top:0"><path d="M18 13v18l13-9z" fill="#fff"/></svg></div>
  </div>
  <div class="video-bar">
    <svg width="8" height="8" viewBox="0 0 8 8"><path d="M1 0v8l6-4z" fill="#555"/></svg>
    <span>00:00:00</span>
    <span style="flex:1;height:3px;background:#ddd;position:relative"><span style="position:absolute;left:0;top:0;width:55%;height:3px;background:var(--orange)"></span></span>
    <svg width="10" height="8" viewBox="0 0 10 8"><path d="M0 2h3l3-2v8L3 6H0z" fill="#555"/></svg>
    <span style="width:40px;height:3px;background:var(--orange)"></span>
  </div>
</div>

<!-- products -->
<h2 class="section-title" style="top:2041px">Our Products</h2>
<div class="title-bar" style="top:2116px"></div>
<div class="abs prod-ring"></div>
<div class="abs prod-core" role="img" aria-label="Close-up of a single cell in blue tones"></div>
<div class="abs prod-node" style="left:343px;top:2200px" role="img" aria-label="Orthobiologics device"><i></i></div>
<div class="abs prod-node" style="left:729px;top:2200px" role="img" aria-label="Radiology device"><i></i></div>
<div class="abs prod-node" style="left:343px;top:2466px" role="img" aria-label="General surgery device"><i></i></div>
<div class="abs prod-node" style="left:729px;top:2466px" role="img" aria-label="Hematology device"><i></i></div>
<div class="abs prod-label left" style="left:53px;top:2220px"><h4>Orthobiologics</h4><p>Sed ut perspiciatis unde omnis iste natus error sit voluptatem accusantium doloremque laudantium, totam rem aperiam, eaque ipsa quaeratione</p></div>
<div class="abs prod-label right" style="left:886px;top:2220px"><h4>Radiology</h4><p>Sed ut perspiciatis unde omnis iste natus error sit voluptatem accusantium doloremque laudantium, totam rem aperiam, eaque ipsa quaeratione</p></div>
<div class="abs prod-label left" style="left:53px;top:2484px"><h4>General Surgery</h4><p>Sed ut perspiciatis unde omnis iste natus error sit voluptatem accusantium doloremque laudantium, totam rem aperiam, eaque ipsa quaeratione</p></div>
<div class="abs prod-label right" style="left:886px;top:2484px"><h4>Hematology</h4><p>Sed ut perspiciatis unde omnis iste natus error sit voluptatem accusantium doloremque laudantium, totam rem aperiam, eaque ipsa quaeratione</p></div>

<!-- testimonials -->
<div class="abs clients" role="img" aria-label="Dark background of faint neural network imagery"></div>
<h2 class="section-title" style="top:2794px;color:#fff"><b style="font-weight:600">WHAT</b> OUR CLIENTS SAY</h2>
<div class="title-bar" style="top:2870px;background:#fff"></div>
<div class="abs quote" style="left:145px;top:2944px"><span class="bracket"></span><p>“Sed ut perspiciatis unde omnis iste natus error sit voluptatem ccusantium doloremque laudantium, totam rem aperiam, eaque ipsa quae ab illo inventore veritatis. ”</p><b>Teodor Marlow</b><div class="stars">★★★★★</div></div>
<div class="abs quote" style="left:471px;top:2944px"><span class="bracket"></span><p>“Sed ut perspiciatis unde omnis iste natus error sit voluptatem ccusantium doloremque laudantium, totam rem aperiam, eaque ipsa quae ab illo inventore veritatis. ”</p><b>Teodor Marlow</b><div class="stars">★★★★★</div></div>
<div class="abs quote" style="left:795px;top:2944px"><span class="bracket"></span><p>“Sed ut perspiciatis unde omnis iste natus error sit voluptatem ccusantium doloremque laudantium, totam rem aperiam, eaque ipsa quae ab illo inventore veritatis. ”</p><b>Teodor Marlow</b><div class="stars">★★★★★</div></div>

<!-- faq -->
<div class="abs faq-bg" role="img" aria-label="Faded photo of a lab worker with glassware"></div>
<h2 class="section-title" style="top:3301px">Frequently Asked Questions</h2>
<div class="title-bar" style="top:3375px"></div>
<div class="abs faq-item" style="top:3420px;height:89px"><span class="faq-plus"></span><span>Does A Small Volume Aspirate Have More Cfu-f Than A Larger Draw<br>That Is Then Volume Reduced By Centrifugation?</span></div>
<div class="abs faq-item" style="top:3524px;height:89px"><span class="faq-plus"></span><span>What Are The Limitations Of Traditional Needles And What Is The Optimal Technique<br>For Minimizing Peripheral Blood Dilution?</span></div>
<div class="abs faq-item" style="top:3636px;height:89px"><span class="faq-plus"></span><span>What Are The Different Techniques To Aspirate Marrow Using A Traditional Needle And<br>What Can I Expect For Cfu-f Per Ml Using Such Techniques?</span></div>
<div class="abs faq-item" style="top:3740px;height:70px"><span class="faq-plus"></span><span>What Is The Importance Of Cfu-f Counts Compared To Nucleated Cell Counts?</span></div>

<!-- contact -->
<div class="abs contact" role="img" aria-label="Blue tinted photo of a lab technician"></div>
<h2 class="section-title" style="top:3973px;color:#fff">Contact Form</h2>
<div class="abs field" style="top:4088px">First Name</div>
<div class="abs field" style="top:4136px">Last Name</div>
<div class="abs field" style="top:4184px">Company Name</div>
<div class="abs field" style="top:4232px">Email Address</div>
<div class="abs field" style="top:4281px">Phone Number</div>
<div class="abs message">Message :</div>
<div class="abs submit">SUBMIT</div>
<svg class="abs" style="left:0;top:4470px" width="1200" height="80" viewBox="0 0 1200 80" preserveAspectRatio="none"><path d="M0 58 Q600 -10 1200 58 V80 H0z" fill="#fff"/></svg>

<!-- footer -->
<div class="abs foot-brand"><span class="brand-dot" style="width:40px;height:40px"></span><span class="brand-name">Coralweave<br>Solutions</span></div>
<div class="abs socials"><span></span><span></span><span></span><span></span></div>

<h3 class="abs foot-h" style="left:338px;top:4576px">SIGN UP FOR NEWSLETTER</h3>
<p class="abs foot-p" style="left:338px;top:4620px;width:280px">Excepteur sint occaecat cupidatat non proident, sunt in culpa qui officia deserunt</p>
<div class="abs news-input">Enter email</div>
<div class="abs subscribe">SUBSCRIBE</div>

<h3 class="abs foot-h" style="left:656px;top:4578px">CONTACT US</h3>
<div class="abs c-row" style="top:4626px"><svg width="16" height="18" viewBox="0 0 24 24"><path fill="var(--blue-bright)" d="M12 2a7 7 0 0 0-7 7c0 5 7 13 7 13s7-8 7-13a7 7 0 0 0-7-7zm0 9.5A2.5 2.5 0 1 1 12 6.5a2.5 2.5 0 0 1 0 5z"/></svg><span>Coralweave Solutions LLC<br>Lanier Road Halden Park, WA, 6104</span></div>
<div class="abs c-row" style="top:4680px"><svg width="16" height="16" viewBox="0 0 24 24"><path fill="var(--blue-bright)" d="M6.6 10.8a15.2 15.2 0 0 0 6.6 6.6l2.2-2.2a1 1 0 0 1 1-.25 11.4 11.4 0 0 0 3.6.57 1 1 0 0 1 1 1V20a1 1 0 0 1-1 1A17 17 0 0 1 3 4a1 1 0 0 1 1-1h3.5a1 1 0 0 1 1 1c0 1.25.2 2.45.57 3.57a1 1 0 0 1-.25 1z"/></svg><span>Phone:<br>+888 7410 2964</span></div>
<div class="abs c-row" style="top:4734px"><svg width="16" height="14" viewBox="0 0 24 20"><path fill="var(--blue-bright)" d="M2 2h20v16H2zm2 2v1l8 5 8-5V4z"/></svg><span>Email:<br>info@coralweavesolutions.com</span></div>

<h3 class="abs foot-h" style="left:955px;top:4576px">QUICK LINKS</h3>
<ul class="abs links"><li>Home</li><li>About Us</li><li>Products</li><li>Blog</li><li>Faq</li><li>Contact Us</li></ul>

<p class="abs copyright">Coralweave Solutions LLC © 2019 All Rights Reserved | Privacy Policy | Terms and Conditions</p>

</body>
</html>
```